New Electrical Business Card Design

I would like a new design for my business cards.
i would like the same logo and font but new design
Please see attached files for front and back design.
large image can be used for graphics.
I would like the instagram link incorporated to back of card.
website site address needs to be changed to www.kestrelhillelectrical.au
everything else stays as is

```html
<!DOCTYPE html>
<html lang="en">
<head>
<meta charset="utf-8">
<title>Kestrel Hill Electrical &amp; Data – Business Card</title>
<link rel="stylesheet" href="https://fonts.googleapis.com/css2?family=Montserrat:wght@400;500;600;800&display=swap">
<style>
  :root {
    --bg: #d4d4d4;
    --white: #ffffff;
    --ink: #1d1d1d;
    --charcoal: #2b2b2c;
    --grey: #7c7c7c;
    --grey-light: #8a8a8a;
    --green: #0d8a43;
    --back-mark: #1f1f20;
  }
  * { box-sizing: border-box; margin: 0; padding: 0; }
  html, body {
    width: 1200px; height: 788px; overflow: hidden;
    background: var(--bg);
    font-family: "Montserrat", sans-serif;
  }
  .canvas {
    width: 1200px; height: 788px;
    display: flex; flex-direction: column;
    align-items: center; justify-content: center; gap: 30px;
  }
  .card {
    position: relative;
    width: 620px; height: 354px;
    border-radius: 22px;
    overflow: hidden;
  }

  /* Front */
  .card-front { background: var(--white); }
  .front-brand {
    position: absolute; left: 34px; top: 52px;
    display: flex; align-items: center; gap: 12px;
  }
  .brand-dot { width: 18px; height: 18px; border-radius: 50%; background: var(--green); }
  .brand-name {
    font-weight: 800; font-size: 38px; letter-spacing: -0.5px;
    color: var(--ink); line-height: 1;
  }
  .registration {
    position: absolute; right: 30px; top: 28px;
    text-align: left; font-size: 13px; line-height: 1.35; color: var(--ink);
  }
  .contact-band {
    position: absolute; left: 0; top: 132px;
    width: 470px; height: 134px;
    background: var(--charcoal);
    padding: 16px 0 0 34px;
  }
  .grey-block {
    position: absolute; left: 470px; top: 102px;
    width: 150px; height: 164px;
    background: var(--grey);
  }
  .feature-circle {
    position: absolute; left: 428px; top: 92px; width: 170px; height: 170px;
  }
  .person-name {
    font-weight: 800; font-size: 20px; color: var(--green);
    letter-spacing: 0.5px; margin-bottom: 8px;
  }
  .contact-list { list-style: none; }
  .contact-list li {
    display: flex; align-items: center; gap: 9px;
    color: var(--white); font-size: 15px; font-weight: 500; line-height: 1.6;
  }
  .contact-list svg { width: 13px; height: 13px; flex: none; }
  .services {
    position: absolute; left: 34px; top: 296px;
    font-size: 18px; font-weight: 500; color: var(--ink);
  }
  .services .sep { color: var(--green); font-weight: 800; padding: 0 4px; }

  /* Back */
  .card-back { background: var(--charcoal); }
  .back-brand {
    position: absolute; left: 0; right: 0; top: 120px;
    text-align: center;
    font-weight: 800; font-size: 62px; letter-spacing: -1px;
    color: var(--back-mark);
  }
  .social {
    position: absolute; left: 0; right: 0; top: 262px;
    display: flex; align-items: center; justify-content: center; gap: 10px;
    color: var(--white); font-size: 17px; font-weight: 500; letter-spacing: 0.3px;
  }
  .social-square {
    width: 15px; height: 15px; border: 2px solid var(--green); border-radius: 4px;
  }
</style>
</head>
<body>
<main class="canvas">

  <section class="card card-front" aria-label="Business card front">
    <div class="front-brand">
      <span class="brand-dot"></span>
      <span class="brand-name">KESTREL HILL</span>
    </div>

    <p class="registration">ABN - 12 345 678 901<br>Lic Number - 100482B</p>

    <div class="grey-block"></div>
    <svg class="feature-circle" viewBox="0 0 170 170" aria-hidden="true">
      <circle cx="85" cy="85" r="80" fill="var(--white)"/>
      <circle cx="85" cy="85" r="70" fill="var(--grey-light)"/>
    </svg>

    <div class="contact-band">
      <p class="person-name">DANIEL MORROW</p>
      <ul class="contact-list">
        <li>
          <svg viewBox="0 0 24 24"><path fill="var(--green)" d="M6.6 10.8a15 15 0 0 0 6.6 6.6l2.2-2.2c.3-.3.7-.4 1-.2 1.1.4 2.3.6 3.6.6.6 0 1 .4 1 1V20c0 .6-.4 1-1 1A17 17 0 0 1 3 4c0-.6.4-1 1-1h3.5c.6 0 1 .4 1 1 0 1.3.2 2.5.6 3.6.1.3 0 .7-.2 1z"/></svg>
          0400 555 183
        </li>
        <li>
          <svg viewBox="0 0 24 24"><rect x="2" y="5" width="20" height="14" rx="2" fill="var(--green)"/><path d="M3 6l9 7 9-7" fill="none" stroke="var(--charcoal)" stroke-width="2"/></svg>
          info@kestrelhillelectrical.au
        </li>
        <li>
          <svg viewBox="0 0 24 24"><circle cx="12" cy="12" r="9" fill="none" stroke="var(--green)" stroke-width="2.5"/><path d="M3 12h18M12 3c3 3 3 15 0 18M12 3c-3 3-3 15 0 18" fill="none" stroke="var(--green)" stroke-width="1.8"/></svg>
          www.kestrelhillelectrical.au
        </li>
      </ul>
    </div>

    <p class="services">Residential<span class="sep">·</span>Commercial<span class="sep">·</span>Industrial<span class="sep">·</span>24hr Service</p>
  </section>

  <section class="card card-back" aria-label="Business card back">
    <p class="back-brand">KESTREL HILL</p>
    <p class="social"><span class="social-square"></span>kestrel.hill.electrical</p>
  </section>

</main>
</body>
</html>
```